wealth management firm, professional group, new model

we have a logo that works but we need a card, white background using our colors...clean look

our tag line if can be used in

Guiding Clients Toward Ownership

```html
<!DOCTYPE html>
<html lang="en">
<head>
<meta charset="utf-8">
<title>Arcova Wealth Partners – Business Card</title>
<link href="https://fonts.googleapis.com/css2?family=Montserrat:wght@400;500&display=swap" rel="stylesheet">
<style>
  :root {
    --stage: #262626;
    --navy: #172a4b;
    --navy-deep: #13233f;
    --paper: #f1f1f1;
    --paper-shade: #e4e4e4;
    --ink: #14264a;
    --light-text: #e6e9ef;
  }
  * { margin: 0; padding: 0; box-sizing: border-box; }
  html, body {
    width: 1200px; height: 576px; overflow: hidden;
    background: var(--stage);
    font-family: "Montserrat", sans-serif;
  }
  .canvas { position: relative; width: 1200px; height: 576px; }

  .card {
    position: absolute;
    top: 138px;
    border-radius: 10px;
    overflow: hidden;
  }

  /* Back side */
  .card-back {
    left: 102px; width: 484px; height: 294px;
    background: linear-gradient(180deg, var(--navy) 0%, var(--navy-deep) 100%);
  }
  .card-back .brand-name {
    position: absolute; left: 0; right: 0; top: 112px;
    text-align: center;
    font-size: 30px; font-weight: 400; letter-spacing: 14px;
    padding-left: 14px;
    color: var(--light-text);
  }
  .card-back .tagline {
    position: absolute; left: 0; right: 0; top: 249px;
    text-align: center;
    font-size: 13.5px; letter-spacing: 0.6px;
    color: var(--light-text);
  }

  /* Front side */
  .card-front {
    left: 596px; width: 480px; height: 291px;
    background: linear-gradient(180deg, var(--paper) 0%, var(--paper-shade) 100%);
    color: var(--ink);
  }
  .brand-block {
    position: absolute; left: 28px; width: 220px; top: 112px;
    text-align: center;
  }
  .brand-block .brand-name {
    font-size: 31px; font-weight: 400; letter-spacing: 10px;
    padding-left: 10px; line-height: 1;
    white-space: nowrap;
  }
  .brand-block .brand-sub {
    margin-top: 22px;
    font-size: 12.5px; font-weight: 400; letter-spacing: 1.9px;
    white-space: nowrap;
  }
  .person {
    position: absolute; right: 34px; top: 56px; text-align: right;
  }
  .person .name { font-size: 20px; font-weight: 500; letter-spacing: 0.4px; line-height: 1.2; }
  .person .role { font-size: 12.5px; letter-spacing: 0.3px; }
  .contacts {
    position: absolute; right: 36px; top: 121px;
    list-style: none; text-align: right;
  }
  .contacts li {
    display: flex; justify-content: flex-end; align-items: center; gap: 8px;
    font-size: 12.5px; height: 20px;
    white-space: nowrap;
  }
  .contacts svg { width: 11px; height: 11px; fill: var(--ink); }
  .tagline-band {
    position: absolute; left: 0; right: 0; top: 236px; height: 39px;
    background: var(--navy);
    color: var(--light-text);
    display: flex; align-items: center; justify-content: center;
    font-size: 13.5px; letter-spacing: 1.1px;
  }
</style>
</head>
<body>
<main class="canvas">

  <section class="card card-back" aria-label="Card back">
    <div class="brand-name">ARCOVA</div>
    <p class="tagline">Guiding Clients Toward Ownership</p>
  </section>

  <section class="card card-front" aria-label="Card front">
    <div class="brand-block">
      <div class="brand-name">ARCOVA</div>
      <div class="brand-sub">WEALTH PARTNERS</div>
    </div>

    <div class="person">
      <div class="name">Evan Marsh</div>
      <div class="role">Managing Director</div>
    </div>

    <ul class="contacts">
      <li>555-014-2876
        <svg viewBox="0 0 24 24" aria-hidden="true"><path d="M3 9c0-3 4-5 9-5s9 2 9 5v2h-5V8.5c-1-.4-2.5-.6-4-.6s-3 .2-4 .6V11H3zM6 12h12l2 8H4z"/></svg>
      </li>
      <li>evan@arcovawealth.com
        <svg viewBox="0 0 24 24" aria-hidden="true"><path d="M2 5h20v14H2zM4 7v.5l8 6 8-6V7z"/></svg>
      </li>
      <li>www.arcovawealth.com
        <svg viewBox="0 0 24 24" aria-hidden="true"><path d="M12 2a10 10 0 1 0 0 20 10 10 0 0 0 0-20zm0 2c1.3 1.5 2.2 3.5 2.5 7h-5c.3-3.5 1.2-5.5 2.5-7zM4.1 11A8 8 0 0 1 9 4.6C8.1 6.3 7.6 8.5 7.5 11zm0 2h3.4c.1 2.5.6 4.7 1.5 6.4A8 8 0 0 1 4.1 13zm5.4 0h5c-.3 3.5-1.2 5.5-2.5 7-1.3-1.5-2.2-3.5-2.5-7zm7 0h3.4a8 8 0 0 1-4.9 6.4c.9-1.7 1.4-3.9 1.5-6.4zm0-2c-.1-2.5-.6-4.7-1.5-6.4a8 8 0 0 1 4.9 6.4z"/></svg>
      </li>
    </ul>

    <div class="tagline-band">GUIDING CLIENTS TOWARD OWNERSHIP</div>
  </section>

</main>
</body>
</html>
```